Brightlane Rapid Rinse Web Design

We are looking for a web design that highlights our state of the art fully automated commercial vehicle washing equipment. Similar system to a car wash however this system is meant for the largest vehicles on our roadways. Transport trucks with or without a trailer, busses both highway and school, RV's from 5th wheel type to A Class. Cement trucks, dump trucks, vac trucks, fuel trucks etc. Pick ups with utility trailers...Refrigerator truck clean outs.
Brightlane Rapid Rinse will wash your vehicle quickly and with a minimal impact on the environment

Home page
About us
Why Brightlane
Services and pricing
Videos of wash system
Fleets
contact us

Target Market(s)

Commercial vehicle owners and operators as well as corporate fleets. Includes busses, municipal, school and highway.both school and

Industry/Entity Type

transportation

Coding

Coded - Design and coding required

Number of Pages Required

5+ page

Font styles to use
Sans Serif

Colors
0054AA
0677BA
7BADD7
CADEEF
E8F1F8

Requirements
Must have
• Welcome page,why us page which describes the financial and environmental benefits. payment processing page, contact us page, Services which is washing vehicles and greasing for commercial vehicles that want that service and grease
Nice to have
• pictures of both clean and dirty commercial vehicles ie. before and after

```html
<!DOCTYPE html>
<html lang="en">
<head>
<meta charset="utf-8">
<title>Brightlane Rapid Rinse</title>
<link href="https://fonts.googleapis.com/css2?family=Poppins:ital,wght@0,400;0,500;0,600;0,700;0,800;1,700;1,800&display=swap" rel="stylesheet">
<style>
:root{
  --blue-deep:#0054AA;
  --blue:#0677BA;
  --blue-mid:#7BADD7;
  --blue-pale:#CADEEF;
  --blue-mist:#E8F1F8;
  --ink:#1c2430;
  --grey-band:#ececec;
  --white:#ffffff;
  --dark:#1a1d22;
}
*{box-sizing:border-box;margin:0;padding:0}
html,body{width:1200px;height:5280px;overflow:hidden}
body{font-family:'Poppins',sans-serif;color:var(--ink);background:var(--white);position:relative}
.section{position:absolute;left:0;width:1200px}
.photo-fill{position:absolute;inset:0}

/* header */
.site-header{top:0;height:88px;background:var(--white);z-index:5;display:flex;align-items:center;justify-content:space-between;padding:0 40px 0 72px}
.brand{display:flex;align-items:center;gap:12px}
.brand-mark{width:22px;height:22px;border-radius:50%;background:var(--blue-deep)}
.brand-name{font-weight:700;font-size:22px;color:var(--blue-deep);letter-spacing:.5px;line-height:1.1}
.main-nav{display:flex;gap:26px}
.main-nav a{font-size:14px;font-weight:600;color:var(--ink);text-decoration:none}
.main-nav a.active{color:var(--blue);border-bottom:2px solid var(--blue);padding-bottom:4px}

/* hero */
.hero{top:88px;height:720px;overflow:hidden;background:#0a2f6b}
.hero-photo{background:
  radial-gradient(ellipse 38% 55% at 50% 40%,rgba(202,222,239,.55),rgba(123,173,215,.25) 45%,rgba(0,0,0,0) 75%),
  radial-gradient(ellipse 30% 70% at 12% 50%,rgba(6,119,186,.7),rgba(0,0,0,0) 70%),
  radial-gradient(ellipse 30% 70% at 88% 55%,rgba(6,119,186,.6),rgba(0,0,0,0) 70%),
  linear-gradient(180deg,#123c7a 0%,#0b4fa0 45%,#0a3677 80%,#071f4a 100%)}
.hero-shade{position:absolute;inset:0;background:rgba(0,40,100,.25)}
.hero-content{position:absolute;top:178px;left:0;width:100%;text-align:center;color:var(--white)}
.hero-title{font-style:italic;font-weight:800;font-size:76px;line-height:1;letter-spacing:1px;text-transform:uppercase}
.hero-sub{font-style:italic;font-weight:800;font-size:56px;line-height:1.05;text-transform:uppercase;margin-top:2px}
.hero-text{font-size:21px;font-weight:600;line-height:1.35;width:700px;margin:18px auto 0}
.hero-buttons{display:flex;justify-content:center;gap:18px;margin-top:34px}
.btn-outline{border:2px solid var(--white);color:var(--white);font-size:14px;font-weight:600;padding:10px 22px;text-transform:uppercase}
.hero-dots{position:absolute;top:676px;left:72px;display:flex;gap:10px}
.hero-dots span{width:12px;height:12px;background:var(--white);opacity:.9}
.hero-edge{position:absolute;left:0;bottom:0;width:1200px;height:90px}

/* mission */
.mission{top:808px;height:440px;background:var(--grey-band)}
.mission-box{position:absolute;left:72px;top:12px;width:1056px;height:420px;overflow:hidden;clip-path:polygon(0 8%,100% 0,100% 100%,0 100%);color:var(--white);text-align:center;padding:110px 70px 0}
.mission-photo{background:
  radial-gradient(ellipse 40% 60% at 20% 40%,rgba(123,173,215,.45),rgba(0,0,0,0) 70%),
  radial-gradient(ellipse 35% 60% at 85% 60%,rgba(202,222,239,.3),rgba(0,0,0,0) 70%),
  linear-gradient(120deg,#0054AA,#0677BA 55%,#0b5fae)}
.mission-inner{position:relative}
.section-title{font-style:italic;font-weight:800;font-size:40px;text-transform:uppercase;letter-spacing:.5px}
.mission-box p{font-size:16px;line-height:1.55;margin-top:18px}
.stripe-svg{position:absolute;left:0;width:1200px}

/* about */
.about{top:1340px;height:620px;background:var(--grey-band)}
.about-frame{position:absolute;left:36px;top:74px;width:140px;height:400px;background:var(--blue-mid);clip-path:polygon(0 0,100% 16%,100% 100%,0 84%)}
.about-photo{position:absolute;left:72px;top:124px;width:516px;height:300px;background:
  radial-gradient(ellipse 45% 55% at 55% 55%,rgba(30,90,170,.95),rgba(0,0,0,0) 70%),
  radial-gradient(ellipse 30% 60% at 90% 40%,rgba(70,160,150,.7),rgba(0,0,0,0) 70%),
  linear-gradient(180deg,#5f7d92 0%,#2c5a84 50%,#3a4550 100%)}
.about-text{position:absolute;left:612px;top:150px;width:520px}
.about-title{font-style:italic;font-weight:800;font-size:44px;line-height:1.08;color:var(--blue-deep);text-transform:uppercase}
.about-text p{font-size:15px;line-height:1.5;margin-top:14px;color:#333}
.btn-solid{display:inline-block;background:var(--blue);color:var(--white);font-size:14px;font-weight:600;padding:12px 26px;text-transform:uppercase;margin-top:22px}

/* services */
.services{top:2040px;height:540px;background:var(--white)}
.services .section-title{color:var(--blue-deep);text-align:center;margin-top:40px}
.service-cards{position:absolute;top:124px;left:72px;display:flex;gap:36px}
.service-card{width:328px;height:340px;position:relative;overflow:hidden}
.service-card .label{position:absolute;left:0;right:0;bottom:0;height:60px;background:rgba(0,84,170,.85);color:var(--white);font-style:italic;font-weight:800;font-size:20px;text-transform:uppercase;display:flex;align-items:center;justify-content:center}

/* pricing */
.pricing{top:2580px;height:990px;clip-path:polygon(0 4%,100% 0,100% 96%,0 100%);background:
  radial-gradient(ellipse 35% 40% at 15% 35%,rgba(120,110,95,.45),rgba(0,0,0,0) 70%),
  radial-gradient(ellipse 35% 40% at 85% 75%,rgba(90,100,115,.45),rgba(0,0,0,0) 70%),
  linear-gradient(160deg,#2b2f35,#15181c 60%,#262a30)}
.pricing .section-title{color:var(--white);text-align:center;margin-top:166px}
.price-cards{position:absolute;top:244px;left:72px;display:flex;gap:20px}
.price-card{width:518px;background:var(--white)}
.price-card .photo{height:236px;position:relative}
.price-body{padding:26px 18px 24px;position:relative}
.price-name{font-style:italic;font-weight:800;font-size:24px;color:var(--blue-deep);text-transform:uppercase}
.price-tag{position:absolute;right:18px;top:-6px;width:96px;height:96px;background:var(--dark);color:var(--white);text-align:center;padding-top:12px}
.price-tag b{font-size:38px;font-weight:800;line-height:1}
.price-tag b sup{font-size:18px;vertical-align:top}
.price-tag span{display:block;font-size:12px}
.price-list{list-style:none;margin-top:14px}
.price-list li{font-size:15px;line-height:1.9;display:flex;align-items:center;gap:10px;color:#333}
.tick{width:14px;height:14px;flex:none}

/* before & after */
.gallery{top:3580px;height:520px;background:var(--white)}
.gallery .section-title{color:var(--blue-deep);text-align:center;margin-top:34px}
.slider{position:absolute;top:92px;left:0;width:1200px;height:370px}
.slide{position:absolute;top:0;height:370px}
.slide-tag{position:absolute;left:12px;bottom:10px;color:var(--white);font-style:italic;font-weight:800;font-size:14px}
.arrow{position:absolute;top:165px;width:24px;height:40px}
.split-knob{position:absolute;left:582px;top:167px;width:36px;height:36px;border-radius:50%;background:var(--white);border:2px solid var(--blue-deep)}

/* contact */
.contact{top:4120px;height:740px;clip-path:polygon(0 6%,100% 0,100% 100%,0 100%);background:
  radial-gradient(ellipse 35% 45% at 80% 30%,rgba(123,173,215,.35),rgba(0,0,0,0) 70%),
  linear-gradient(135deg,#0f4f9c,#0054AA 50%,#1266b6)}
.contact-photo{position:absolute;left:72px;top:184px;width:520px;height:396px;background:
  radial-gradient(ellipse 40% 45% at 35% 50%,rgba(190,80,40,.9),rgba(0,0,0,0) 70%),
  radial-gradient(ellipse 30% 50% at 85% 60%,rgba(60,120,170,.7),rgba(0,0,0,0) 70%),
  linear-gradient(180deg,#6a6f78,#7a4a38 55%,#3e4350)}
.contact-form{position:absolute;left:612px;top:206px;width:516px}
.contact-form .section-title{color:var(--white);text-align:left}
.field-row{display:flex;gap:16px;margin-top:16px}
.field{flex:1;height:48px;background:var(--white);font-size:13px;color:#888;padding:14px 12px}
.field.message{height:120px}
.contact-form .btn-solid{background:var(--blue);border:2px solid var(--white);margin-top:18px}

/* footer */
.site-footer{top:4860px;height:420px;background:var(--white)}
.footer-brand{position:absolute;left:72px;top:120px}
.footer-copy{font-size:12px;line-height:1.5;margin-top:26px;color:#333}
.socials{display:flex;gap:12px;margin-top:20px}
.socials span{width:18px;height:18px;border-radius:50%;background:var(--blue-deep)}
.footer-col{position:absolute;top:110px}
.footer-col h4{font-style:italic;font-weight:800;font-size:20px;color:var(--blue-deep);text-transform:uppercase;margin-bottom:12px}
.footer-col a{display:block;font-size:14px;line-height:1.75;color:#333;text-decoration:none}
.contact-item{display:flex;gap:12px;align-items:center;font-size:13px;line-height:1.5;margin-bottom:14px;color:#333}
.contact-icon{width:34px;height:34px;flex:none}
</style>
</head>
<body>

<header class="section site-header">
  <div class="brand"><span class="brand-mark"></span><span class="brand-name">BRIGHTLANE<br>RAPID RINSE</span></div>
  <nav class="main-nav">
    <a class="active" href="#">HOME</a><a href="#">ABOUT US</a><a href="#">WHY BRIGHTLANE</a><a href="#">SERVICES</a><a href="#">PRICING</a><a href="#">VIDEOS</a><a href="#">FLEETS</a><a href="#">CONTACT US</a>
  </nav>
</header>

<section class="section hero">
  <div class="photo-fill hero-photo" role="img" aria-label="Truck inside an automated wash bay lit in blue"></div>
  <div class="hero-shade"></div>
  <div class="hero-content">
    <h1 class="hero-title">Brightlane</h1>
    <div class="hero-sub">Rapid Rinse</div>
    <p class="hero-text">Temporibus autem quibusdam et aut officiis debitis aut rerum necessitatibus saepe eveniet ut et voluptates repudiandae sint.</p>
    <div class="hero-buttons"><span class="btn-outline">Book a Wash</span><span class="btn-outline">Learn More</span><span class="btn-outline">Contact Us</span></div>
  </div>
  <div class="hero-dots"><span></span><span></span><span></span><span></span></div>
  <svg class="hero-edge" viewBox="0 0 1200 90" preserveAspectRatio="none">
    <polygon points="0,90 1200,0 1200,90" fill="#ececec"/>
    <polygon points="540,60 1200,4 1200,14 540,70" fill="#0677BA"/>
  </svg>
</section>

<section class="section mission">
  <div class="mission-box">
    <div class="photo-fill mission-photo" role="img" aria-label="Wash bay interior tinted blue"></div>
    <div class="mission-inner">
      <h2 class="section-title">Our Mission</h2>
      <p>Sed ut perspiciatis unde omnis iste natus error sit voluptatem accusantium doloremque laudantium, totam rem aperiam, eaque ipsa quae ab illo inventore veritatis et quasi architecto beatae vitae dicta sunt explicabo. Nemo enim ipsam voluptatem quia voluptas sit aspernatur aut odit aut fugit, sed quia consequuntur magni dolores eos qui ratione voluptatem.</p>
    </div>
  </div>
</section>
<svg class="stripe-svg" style="top:1230px;height:110px" viewBox="0 0 1200 110" preserveAspectRatio="none">
  <polygon points="0,20 1200,0 1200,110 0,110" fill="#ffffff"/>
  <polygon points="0,110 1200,40 1200,110" fill="#ececec"/>
  <polygon points="760,60 1200,34 1200,44 760,70" fill="#7BADD7"/>
</svg>

<section class="section about">
  <div class="about-frame"></div>
  <div class="about-photo" role="img" aria-label="Blue semi truck parked in a wash bay"></div>
  <div class="about-text">
    <h2 class="about-title">About Brightlane<br>Rapid Rinse</h2>
    <p>Sed ut perspiciatis unde omnis iste natus error sit voluptatem accusantium doloremque laudantium, totam rem aperiam, eaque ipsa quae ab illo inventore veritatis et quasi architecto beatae vitae dicta sunt explicabo. Nemo enim ipsam voluptatem quia voluptas sit aspernatur aut odit aut fugit, sed quia consequuntur magni dolores eos qui ratione voluptatem.</p>
    <span class="btn-solid">Read More</span>
  </div>
</section>
<svg class="stripe-svg" style="top:1930px;height:90px" viewBox="0 0 1200 90" preserveAspectRatio="none">
  <polygon points="0,0 1200,0 1200,20 0,90" fill="#ececec"/>
  <polygon points="0,70 640,34 640,44 0,80" fill="#0677BA"/>
</svg>

<section class="section services">
  <h2 class="section-title">Our Services</h2>
  <div class="service-cards">
    <div class="service-card"><div class="photo-fill" role="img" aria-label="Truck passing through pink rotating wash brushes" style="background:radial-gradient(ellipse 50% 40% at 50% 35%,rgba(230,80,180,.9),rgba(0,0,0,0) 70%),linear-gradient(180deg,#6a3a78,#9a2a7a 45%,#3a3f4a)"></div><div class="label">Automated Truck Wash</div></div>
    <div class="service-card"><div class="photo-fill" role="img" aria-label="Worker pressure washing a vehicle in a bay" style="background:radial-gradient(ellipse 50% 50% at 60% 40%,rgba(240,220,190,.9),rgba(0,0,0,0) 70%),linear-gradient(180deg,#a88a68,#c9a880 50%,#6f5a48)"></div><div class="label">Additional Services</div></div>
    <div class="service-card"><div class="photo-fill" role="img" aria-label="Row of white fleet vans under a blue sky" style="background:radial-gradient(ellipse 60% 30% at 55% 62%,rgba(255,255,255,.95),rgba(0,0,0,0) 75%),linear-gradient(180deg,#3f82c0,#9dbfdc 50%,#b7bec6)"></div><div class="label">Fleet Services</div></div>
  </div>
</section>

<section class="section pricing">
  <h2 class="section-title">Pricing Packages</h2>
  <div class="price-cards">
    <div class="price-card">
      <div class="photo" role="img" aria-label="Worker beside an orange and grey refuse truck" style="background:radial-gradient(ellipse 30% 50% at 25% 60%,rgba(230,110,40,.9),rgba(0,0,0,0) 70%),radial-gradient(ellipse 40% 50% at 70% 50%,rgba(150,155,160,.9),rgba(0,0,0,0) 70%),linear-gradient(180deg,#b9c3cc,#7d838a 60%,#4a4f56)"></div>
      <div class="price-body">
        <div class="price-tag"><b><sup>$</sup>59</b><span>Per Month</span></div>
        <div class="price-name">Individual Pricing</div>
        <ul class="price-list">
          <li><svg class="tick" viewBox="0 0 14 14"><path d="M2 7l3 3 7-7" fill="none" stroke="#0677BA" stroke-width="2"/></svg>Sed ut perspiciatis unde omnis iste</li>
          <li><svg class="tick" viewBox="0 0 14 14"><path d="M2 7l3 3 7-7" fill="none" stroke="#0677BA" stroke-width="2"/></svg>Natus error sit voluptatem</li>
          <li><svg class="tick" viewBox="0 0 14 14"><path d="M2 7l3 3 7-7" fill="none" stroke="#0677BA" stroke-width="2"/></svg>Accusantium doloremque laudantium</li>
          <li><svg class="tick" viewBox="0 0 14 14"><path d="M2 7l3 3 7-7" fill="none" stroke="#0677BA" stroke-width="2"/></svg>Totam rem aperiam, eaque ipsa quae ab illo inventore</li>
          <li><svg class="tick" viewBox="0 0 14 14"><path d="M2 7l3 3 7-7" fill="none" stroke="#0677BA" stroke-width="2"/></svg>Veritatis et quasi architecto beatae</li>
        </ul>
        <span class="btn-solid">More Info</span>
      </div>
    </div>
    <div class="price-card">
      <div class="photo" role="img" aria-label="White delivery vans parked in a row" style="background:radial-gradient(ellipse 60% 30% at 50% 60%,rgba(255,255,255,.95),rgba(0,0,0,0) 75%),linear-gradient(180deg,#2f6db0,#8fb3d6 45%,#9aa2aa 80%,#6b7279)"></div>
      <div class="price-body">
        <div class="price-tag"><b><sup>$</sup>75</b><span>Per Month</span></div>
        <div class="price-name">Fleet Packages</div>
        <ul class="price-list">
          <li><svg class="tick" viewBox="0 0 14 14"><path d="M2 7l3 3 7-7" fill="none" stroke="#0677BA" stroke-width="2"/></svg>Sed ut perspiciatis unde omnis iste</li>
          <li><svg class="tick" viewBox="0 0 14 14"><path d="M2 7l3 3 7-7" fill="none" stroke="#0677BA" stroke-width="2"/></svg>Natus error sit voluptatem</li>
          <li><svg class="tick" viewBox="0 0 14 14"><path d="M2 7l3 3 7-7" fill="none" stroke="#0677BA" stroke-width="2"/></svg>Accusantium doloremque laudantium</li>
          <li><svg class="tick" viewBox="0 0 14 14"><path d="M2 7l3 3 7-7" fill="none" stroke="#0677BA" stroke-width="2"/></svg>Totam rem aperiam, eaque ipsa quae ab illo inventore</li>
          <li><svg class="tick" viewBox="0 0 14 14"><path d="M2 7l3 3 7-7" fill="none" stroke="#0677BA" stroke-width="2"/></svg>Veritatis et quasi architecto beatae</li>
        </ul>
        <span class="btn-solid">More Info</span>
      </div>
    </div>
  </div>
</section>

<section class="section gallery">
  <h2 class="section-title">Before &amp; After</h2>
  <div class="slider">
    <div class="slide" role="img" aria-label="Clean red truck cab after washing" style="left:0;width:272px;background:radial-gradient(ellipse 50% 50% at 40% 45%,rgba(210,60,60,.95),rgba(0,0,0,0) 70%),linear-gradient(180deg,#d8d4d0,#8e2a2a 50%,#4a3a3a)"><span class="slide-tag">AFTER</span></div>
    <div class="slide" role="img" aria-label="Dirty bus front before washing" style="left:312px;width:288px;background:radial-gradient(ellipse 50% 40% at 50% 40%,rgba(200,195,175,.9),rgba(0,0,0,0) 70%),linear-gradient(180deg,#a29e90,#8d8a7e 50%,#5f5d58)"><span class="slide-tag">BEFORE</span></div>
    <div class="slide" role="img" aria-label="Clean bus front after washing" style="left:600px;width:280px;background:radial-gradient(ellipse 50% 40% at 50% 40%,rgba(255,255,255,.95),rgba(0,0,0,0) 70%),linear-gradient(180deg,#c9d0d6,#e3e7ea 50%,#8d97a2)"><span class="slide-tag">AFTER</span></div>
    <div class="slide" role="img" aria-label="Muddy truck wheels before washing" style="left:930px;width:270px;background:radial-gradient(ellipse 45% 45% at 45% 60%,rgba(60,40,35,.9),rgba(0,0,0,0) 70%),linear-gradient(180deg,#b07a5a,#8a5a44 50%,#4a3a34)"><span class="slide-tag">BEFORE</span></div>
    <div class="split-knob"></div>
    <svg class="arrow" style="left:278px" viewBox="0 0 24 40"><path d="M18 4L6 20l12 16" fill="none" stroke="#1c2430" stroke-width="4"/></svg>
    <svg class="arrow" style="left:896px" viewBox="0 0 24 40"><path d="M6 4l12 16L6 36" fill="none" stroke="#1c2430" stroke-width="4"/></svg>
  </div>
</section>

<section class="section contact">
  <div class="contact-photo" role="img" aria-label="Vacuum tank truck in a wash bay with a worker"></div>
  <div class="contact-form">
    <h2 class="section-title">Contact Us</h2>
    <div class="field-row" style="margin-top:22px"><div class="field">First Name</div><div class="field">Last Name</div></div>
    <div class="field-row"><div class="field">Email Address</div><div class="field">Phone No</div></div>
    <div class="field-row"><div class="field message">Message</div></div>
    <span class="btn-solid">Submit</span>
  </div>
</section>

<footer class="section site-footer">
  <div class="footer-brand">
    <div class="brand"><span class="brand-mark"></span><span class="brand-name">BRIGHTLANE<br>RAPID RINSE</span></div>
    <p class="footer-copy">Copyright © 2024 Brightlane Rapid Rinse<br>All Rights Reserved</p>
    <div class="socials" aria-label="Social links"><span></span><span></span><span></span><span></span><span></span></div>
  </div>
  <div class="footer-col" style="left:412px">
    <h4>Quick Links</h4>
    <a href="#">Home</a><a href="#">About Us</a><a href="#">Why Brightlane</a><a href="#">Services</a><a href="#">Pricing</a><a href="#">Videos of Wash System</a><a href="#">Fleets</a><a href="#">Contact Us</a>
  </div>
  <div class="footer-col" style="left:664px">
    <h4>Services</h4>
    <a href="#">Automated Truck Wash</a><a href="#">Additional Services</a><a href="#">Fleet Services</a>
  </div>
  <div class="footer-col" style="left:884px">
    <h4>Contact Info</h4>
    <div class="contact-item"><svg class="contact-icon" viewBox="0 0 34 34"><circle cx="17" cy="17" r="16" fill="none" stroke="#1c2430" stroke-width="1.5"/><path d="M17 9a6 6 0 0 0-6 6c0 5 6 11 6 11s6-6 6-11a6 6 0 0 0-6-6z" fill="#1c2430"/><circle cx="17" cy="15" r="2" fill="#fff"/></svg><span>48 Harbor Line Rd, Unit 7,<br>Millbrook 20415</span></div>
    <div class="contact-item"><svg class="contact-icon" viewBox="0 0 34 34"><circle cx="17" cy="17" r="16" fill="none" stroke="#1c2430" stroke-width="1.5"/><path d="M12 10l3 0 1.5 4-2 1.5a9 9 0 0 0 4 4l1.5-2 4 1.5v3c0 1-1 2-2 2A13 13 0 0 1 10 12c0-1 1-2 2-2z" fill="#1c2430"/></svg><span>+1 555-014-2290</span></div>
    <div class="contact-item"><svg class="contact-icon" viewBox="0 0 34 34"><circle cx="17" cy="17" r="16" fill="none" stroke="#1c2430" stroke-width="1.5"/><rect x="9" y="11" width="16" height="12" fill="none" stroke="#1c2430" stroke-width="1.8"/><path d="M9 11l8 7 8-7" fill="none" stroke="#1c2430" stroke-width="1.8"/></svg><span>hello@brightlanerinse.example</span></div>
  </div>
</footer>

</body>
</html>
```